Homemaking training schools needs a Business Card design

Designer, Hello!

No special requirements, good-looking enough.
--------------------------------------------------------------------------

Name: Marcus Dole
Chairman
Tel: 0574-71948263
Mobile: 13857420916
Email: kelvora@mailnest.example
Web: www.prt2019.example
Add: No.258, LanpingJie, BeiyuanQu, Ningbo, Zhejiang

LOGO
Ningbo PRT Homemaking Training School

Target Market(s)

pregnant women, mothers, infants, the elderly and families, including cleaning, cooking, nursing training.

Industry/Entity Type

Business

Contact Information for Business Card

Name: Marcus Dole
Chairman
Tel: 0574-71948263
Mobile: 13857420916
Email: kelvora@mailnest.example
Web: www.prt2019.example

LOGO

Font styles to use
Serif
Sans Serif
Decorative

Requirements
Nice to have
• Feels: clean, specifications, safety, comfort, warmth and happiness.

```html
<!DOCTYPE html>
<html lang="en">
<head>
<meta charset="utf-8">
<title>PingRuiTian Business Card</title>
<link rel="stylesheet" href="https://fonts.googleapis.com/css2?family=Arimo:wght@400;700&display=swap">
<style>
  :root {
    --stage: #e9e6e1;
    --paper: #ffffff;
    --brand-blue: #1f6fb4;
    --brand-blue-dark: #195a93;
    --brand-pink: #e6007e;
    --ink-light: #ffffff;
    --ink-muted: #555555;
    --rule-grey: #7d7d7d;
    --mark-grey: #e4e7ec;
  }
  * { box-sizing: border-box; margin: 0; padding: 0; }
  html, body {
    width: 1200px; height: 950px; overflow: hidden;
    background: var(--stage);
    font-family: "Arimo", Arial, sans-serif;
  }
  .sheet {
    position: relative; width: 1200px; height: 950px;
    display: flex; flex-direction: column; align-items: center; justify-content: center; gap: 50px;
  }
  .card {
    position: relative; width: 700px; height: 400px; overflow: hidden;
    box-shadow: 0 6px 18px rgba(0,0,0,0.18);
  }

  /* Front */
  .card-front { background: var(--paper); }
  .brand {
    position: absolute; top: 0; left: 0; width: 100%; height: 188px;
    display: flex; flex-direction: column; align-items: center; justify-content: center; padding-top: 30px;
  }
  .brand-name {
    font-weight: 700; font-size: 44px; line-height: 1; color: var(--brand-blue);
  }
  .brand-tagline {
    display: flex; align-items: center; gap: 8px; margin-top: 10px;
    font-size: 14px; color: var(--ink-muted); letter-spacing: 0.5px;
  }
  .brand-tagline::before, .brand-tagline::after {
    content: ""; width: 60px; height: 1px; background: var(--rule-grey);
  }
  .name-band {
    position: absolute; top: 188px; left: 0; width: 100%; height: 72px;
    background: var(--brand-pink); color: var(--ink-light);
    display: flex; flex-direction: column; align-items: center; justify-content: center;
  }
  .person-name { font-weight: 700; font-size: 24px; line-height: 1.2; }
  .person-title { font-size: 16px; line-height: 1.2; margin-top: 2px; }
  .band-rule { position: absolute; top: 260px; left: 0; width: 100%; height: 3px; background: var(--paper); }
  .contact-block {
    position: absolute; top: 263px; left: 0; width: 100%; bottom: 0;
    background: var(--brand-blue); color: var(--ink-light);
    padding: 24px 28px; font-size: 17px; line-height: 1.6;
  }
  .contact-block p { white-space: nowrap; }
  .contact-block b { font-weight: 700; }

  /* Back */
  .card-back {
    background: linear-gradient(135deg, var(--brand-blue) 0%, var(--brand-blue-dark) 100%);
    display: flex; flex-direction: column; align-items: center; justify-content: center; gap: 36px;
  }
  .back-name { color: var(--mark-grey); font-weight: 700; font-size: 44px; line-height: 1; }
  .back-web { color: var(--ink-light); font-size: 18px; letter-spacing: 4px; }
</style>
</head>
<body>
<main class="sheet">
  <section class="card card-front" aria-label="Business card front">
    <div class="brand">
      <div class="brand-name">PingRuiTian</div>
      <div class="brand-tagline">Training &amp; Services</div>
    </div>
    <div class="name-band">
      <div class="person-name">Marcus Dole</div>
      <div class="person-title">Chairman</div>
    </div>
    <div class="band-rule"></div>
    <div class="contact-block">
      <p>No.258, LanpingJie, BeiyuanQu, Ningbo, Zhejiang | <b>P:</b> 0574-71948263</p>
      <p><b>M:</b> 13857420916 <b>E:</b> kelvora@mailnest.example <b>W:</b> www.prt2019.example</p>
    </div>
  </section>

  <section class="card card-back" aria-label="Business card back">
    <div class="back-name">PingRuiTian</div>
    <div class="back-web">www.prt2019.example</div>
  </section>
</main>
</body>
</html>
```